Silvermoor Property Development Co.

We need a logo and business card design for a Hong Kong based real estate company, PLX Land. We are want the brand to reflect the owners forward thinking, creative, and trend setting projects, while also reflecting a sense of security and strength. We invest in industrial properties which we convert to co-living or co-working spaces. PLX stands for Greater Bay Area which is the region around southern China including HK, Macau, and 9 other Chinese cities...made up of approx. 68 million people. There are massive infrastructure projects including the bridge to Macau and high-speed rail to SZ and the bridge connecting SZ and Zhongshan.

Target Market(s)

Chinese and western retail investors, as well as institutional investors

Industry/Entity Type

Real Estate Development

Contact Information for Business Card

Dale Whitford
CEO
dale@plxland-example.com
M + 852 9581 4062
F + 852 3864 2217
Suite 2207, The Halvern, 41 Tremont Rd., Central, Hong Kong

Logo Text

plx land (company name) lifestyle property development (underneath)

Colors

Designer to choose colors to be used in the design.

Requirements
Must have
• Details listed above. One side should include the logo and company name...plx land in modern, hip styling with "lifestyle property development"
Nice to have
• Could be a Black card, with metallic purple "plx" and white "land"...but open great design ideas
Should not have
• boring and traditional layout

```html
<!DOCTYPE html>
<html lang="en">
<head>
<meta charset="utf-8">
<title>PLX Land business card</title>
<link rel="stylesheet" href="https://fonts.googleapis.com/css2?family=Nunito+Sans:wght@400;700;800&display=swap">
<style>
  :root {
    --backdrop: #e4e4e4;
    --paper: #ececec;
    --charcoal: #353535;
    --ink: #4a4a4a;
    --ink-soft: #5e5e5e;
    --accent: #7d4fa3;
    --rule: #b9b9b9;
    --white: #ffffff;
    --white-soft: #cfcfcf;
  }
  * { margin: 0; padding: 0; box-sizing: border-box; }
  html, body {
    width: 1200px; height: 1114px; overflow: hidden;
    background: var(--backdrop);
    font-family: "Nunito Sans", Arial, sans-serif;
  }
  .card {
    position: absolute; left: 150px; width: 900px; height: 498px;
    box-shadow: 0 2px 6px rgba(0,0,0,.18);
  }
  .card--front { top: 39px; background: var(--paper); color: var(--ink); }
  .card--back { top: 577px; background: var(--charcoal); color: var(--white); }

  .company-name { position: absolute; font-weight: 700; line-height: 1; }
  .card--front .company-name { right: 58px; top: 70px; font-size: 60px; color: var(--ink); }
  .card--back .company-name { left: 0; right: 0; top: 170px; text-align: center; font-size: 100px; color: var(--white); }

  .tagline { position: absolute; font-weight: 400; letter-spacing: 1px; }
  .card--front .tagline { left: 64px; top: 78px; font-size: 18px; color: var(--ink-soft); }
  .card--back .tagline { left: 0; right: 0; top: 378px; text-align: center; font-size: 20px; color: var(--white-soft); }

  .website {
    position: absolute; left: 0; right: 0; top: 422px; text-align: center;
    font-size: 20px; letter-spacing: 2px; font-weight: 400; color: var(--white);
  }

  .person { position: absolute; left: 64px; top: 236px; }
  .person__name { font-size: 34px; font-weight: 800; color: var(--ink); line-height: 1.1; }
  .person__title { font-size: 20px; color: var(--ink-soft); margin-top: 2px; }

  .divider {
    position: absolute; left: 62px; right: 58px; top: 344px;
    border-top: 1.5px solid var(--rule);
  }

  .contact { position: absolute; left: 62px; top: 370px; list-style: none; }
  .contact__item {
    display: flex; align-items: center; gap: 14px;
    font-size: 20px; line-height: 29px; color: var(--ink-soft);
  }
  .contact__icon { width: 18px; height: 18px; flex: none; }

  .address {
    position: absolute; right: 58px; top: 370px; text-align: right;
    font-style: normal; font-size: 20px; line-height: 29px; color: var(--ink-soft);
  }
</style>
</head>
<body>

<section class="card card--front" aria-label="Business card front">
  <div class="tagline">Lifestyle Property Development</div>
  <div class="company-name">PLX Land</div>

  <div class="person">
    <div class="person__name">Dale Whitford</div>
    <div class="person__title">CEO</div>
  </div>

  <div class="divider"></div>

  <ul class="contact">
    <li class="contact__item">
      <svg class="contact__icon" viewBox="0 0 24 24" fill="none" stroke="#7d4fa3" stroke-width="2" stroke-linejoin="round"><path d="M5 3h4l2 5-2.5 1.5a11 11 0 0 0 6 6L16 13l5 2v4a2 2 0 0 1-2 2A17 17 0 0 1 3 5a2 2 0 0 1 2-2z"/></svg>
      + 852 3864 2217
    </li>
    <li class="contact__item">
      <svg class="contact__icon" viewBox="0 0 24 24" fill="none" stroke="#7d4fa3" stroke-width="2"><rect x="7" y="2" width="10" height="20" rx="2"/><line x1="11" y1="18" x2="13" y2="18"/></svg>
      + 852 9581 4062
    </li>
    <li class="contact__item">
      <svg class="contact__icon" viewBox="0 0 24 24" fill="none" stroke="#7d4fa3" stroke-width="2"><rect x="2" y="5" width="20" height="14"/><path d="M2 5l10 8 10-8"/></svg>
      dale@plxland-example.com
    </li>
  </ul>

  <address class="address">
    Suite 2207, The Halvern<br>
    41 Tremont Rd.<br>
    Central, Hong Kong
  </address>
</section>

<section class="card card--back" aria-label="Business card back">
  <div class="company-name">PLX Land</div>
  <div class="tagline">Lifestyle Property Development</div>
  <div class="website">www.plxland-example.com</div>
</section>

</body>
</html>
```